Looking for a modern, Professional business card design

We have a simple business card, but are looking for a more modern, professional look. A sample of the basic card is attached as well as the logo. We would also like to add that we offer:
Struggling with your finances?
- Learn to become debt free
- Discover the power of cash
- Control your money instead of it controlling you
Let us help you achieve a new level of financial freedom!
Also, we would like to have a "SPECIAL OFFER!: FREE 30 minute consultation"
Financial Planning

```html
<!DOCTYPE html>
<html lang="en">
<head>
<meta charset="utf-8">
<title>Meadowline Money Coaching – Business Card</title>
<link rel="stylesheet" href="https://fonts.googleapis.com/css2?family=Arimo:ital,wght@0,400;0,700;1,400&display=swap">
<style>
  :root {
    --page-bg: #ece9e4;
    --ink: #1d1d1d;
    --ink-soft: #4a4a4a;
    --green-deep: #2f9a32;
    --green-mid: #5cb947;
    --green-light: #9fd86a;
    --green-text: #6cbd4a;
    --white: #ffffff;
    --card-shadow: 0 14px 30px rgba(0,0,0,.22);
  }
  * { box-sizing: border-box; margin: 0; padding: 0; }
  html, body { width: 1200px; height: 1023px; overflow: hidden; }
  body {
    background: var(--page-bg);
    font-family: "Arimo", Arial, sans-serif;
    display: flex; flex-direction: column; align-items: center; justify-content: center;
    gap: 70px;
  }
  .card {
    width: 640px; height: 366px; border-radius: 22px;
    position: relative; overflow: hidden; box-shadow: var(--card-shadow);
  }

  /* Front */
  .card--front { background: linear-gradient(135deg, #ffffff 0%, #f2f2f2 100%); }
  .emblem-area {
    position: absolute; right: 0; top: 0; width: 300px; height: 100%;
    background: radial-gradient(circle at 30% 35%, var(--green-light) 0%, var(--green-mid) 50%, var(--green-deep) 100%);
    border-top-left-radius: 0 0; clip-path: ellipse(100% 90% at 100% 10%);
  }
  .brand {
    position: absolute; left: 40px; top: 42px;
    display: flex; align-items: center; gap: 12px;
  }
  .brand__dot { width: 26px; height: 26px; border-radius: 50%; background: var(--green-mid); }
  .brand__name { font-weight: 700; font-size: 26px; color: var(--ink); letter-spacing: .5px; line-height: 1.05; }
  .brand__tagline { position: absolute; left: 78px; top: 104px; font-size: 10px; color: var(--ink-soft); }
  .contact { position: absolute; left: 40px; bottom: 34px; }
  .contact__name { font-size: 26px; font-weight: 700; color: var(--green-text); }
  .contact__role { font-size: 14px; color: var(--ink-soft); margin: 4px 0 16px; }
  .contact__list { list-style: none; font-size: 15px; color: var(--ink); }
  .contact__list li { display: flex; align-items: center; gap: 10px; margin-top: 7px; }
  .contact__list svg { width: 14px; height: 14px; flex: none; }

  /* Back */
  .card--back {
    background: radial-gradient(circle at 55% 55%, #8ed35e 0%, #5cb947 45%, #2f9a32 100%);
    color: var(--white); padding: 36px 56px;
  }
  .offer__label { font-size: 19px; font-weight: 700; text-decoration: underline; text-align: center; }
  .offer__headline { font-size: 21px; font-weight: 700; text-align: center; margin: 8px 0 12px; }
  .offer__list { list-style: none; font-size: 16px; line-height: 1.35; }
  .offer__list li::before { content: "• "; }
  .offer__pitch { font-size: 16px; margin-top: 10px; line-height: 1.35; }
  .offer__pitch strong { font-weight: 700; }
  .offer__amp { text-align: center; font-weight: 700; font-size: 20px; margin: 4px 0; }
  .offer__special { font-size: 16px; }
  .offer__special strong { font-weight: 700; }
</style>
</head>
<body>

<section class="card card--front" aria-label="Business card front">
  <div class="emblem-area" role="img" aria-label="Green emblem area with the company's figure mark"></div>
  <div class="brand">
    <span class="brand__dot"></span>
    <span class="brand__name">MEADOWLINE<br>MONEY COACHING</span>
  </div>
  <p class="brand__tagline">Reach a new level of personal calm</p>
  <div class="contact">
    <p class="contact__name">Daniel R. Hale</p>
    <p class="contact__role">Personal Financial Coach</p>
    <ul class="contact__list">
      <li><svg viewBox="0 0 14 14"><circle cx="7" cy="7" r="6.5" fill="none" stroke="#6cbd4a"/><path d="M4.5 4l1.5 0 .7 1.8-.9.7a5 5 0 0 0 1.8 1.8l.7-.9 1.8.7v1.5c-3 .5-6-2.5-5.6-5.6z" fill="#6cbd4a"/></svg>(555) 014-2387</li>
      <li><svg viewBox="0 0 14 14"><rect x="1" y="3" width="12" height="8" fill="#6cbd4a"/><path d="M1 3l6 5 6-5" fill="none" stroke="#fff"/></svg>daniel@meadowlinemoney.com</li>
      <li><svg viewBox="0 0 14 14"><circle cx="7" cy="7" r="6" fill="#6cbd4a"/><path d="M1 7h12M7 1c-3 3-3 9 0 12M7 1c3 3 3 9 0 12" fill="none" stroke="#fff" stroke-width=".8"/></svg>www.meadowlinemoney.com</li>
    </ul>
  </div>
</section>

<section class="card card--back" aria-label="Business card back">
  <p class="offer__label">We Offer</p>
  <p class="offer__headline">Struggling with your finances?</p>
  <ul class="offer__list">
    <li>Learn to become debt free</li>
    <li>Discover the power of cash</li>
    <li>Control your money instead of it controlling you</li>
  </ul>
  <p class="offer__pitch">Let us help you achieve a new level of <strong>financial freedom!</strong></p>
  <p class="offer__amp">&amp;</p>
  <p class="offer__special"><strong>SPECIAL OFFER!:</strong> FREE 30 minute consultation</p>
</section>

</body>
</html>
```